Professional looking Roller Blind Discount Card that portrays quality at a value for money price!

We need a double sided business card designed as a discount card. Size 90mm wide x 55mm high.We would like it to look professional and portray quality at a value for money price point.I have uploaded a word document with a basic layout with the information we want included on each side of the card. Please put your own thought into the layout.

Contact Information for Business Card

As per word document attached.

```html
<!DOCTYPE html>
<html lang="en">
<head>
<meta charset="utf-8">
<title>B&amp;K Interiors – Roller Blind Discount Card</title>
<link href="https://fonts.googleapis.com/css2?family=Arimo:wght@400;700&display=swap" rel="stylesheet">
<style>
  :root{
    --bg:#dcdcdc;
    --blue:#22a6dd;
    --blue-light:#36bde9;
    --grey:#6b6c6e;
    --text:#58595b;
    --white:#ffffff;
    --brown:#7a6657;
    --photo-dark:#5d4a3c;
    --photo-green:#6f8f5a;
    --gold:#f2b61f;
    --gold-dark:#c98a0e;
  }
  *{box-sizing:border-box;margin:0;padding:0}
  html,body{width:1200px;height:900px;overflow:hidden}
  body{background:var(--bg);font-family:"Arimo",Arial,sans-serif;position:relative}
  .card{position:absolute;left:280px;width:640px;height:391px;overflow:hidden;background:var(--white);box-shadow:0 6px 18px rgba(0,0,0,.18)}
  .card--front{top:34px}
  .card--back{top:475px}

  /* front */
  .front-band{position:absolute;left:0;top:0;width:100%;height:185px;background:linear-gradient(160deg,var(--blue-light),var(--blue))}
  .brand{position:absolute;display:flex;align-items:center;gap:12px;color:var(--white);font-weight:700;letter-spacing:1px}
  .front-band .brand{left:200px;top:82px;font-size:28px}
  .brand-mark{width:22px;height:22px;background:var(--white)}
  .offer-ribbon{position:absolute;left:180px;top:172px;width:300px;height:60px}
  .offer-ribbon span{position:absolute;inset:0;display:flex;align-items:center;justify-content:center;color:var(--white);font-weight:700;font-size:36px;padding-top:6px}
  .offer-copy{position:absolute;left:190px;top:248px;color:var(--text);font-size:19px;line-height:24px}
  .badges{position:absolute;left:455px;top:296px;display:flex;gap:10px}
  .badge{width:40px;height:40px;border-radius:50%;background:radial-gradient(circle at 40% 35%,#ffe27a,var(--gold) 55%,var(--gold-dark));box-shadow:0 2px 3px rgba(0,0,0,.25)}
  .call-line{position:absolute;left:190px;top:345px;color:var(--text);font-size:22px}
  .call-line strong{color:var(--blue);font-weight:700}

  /* back */
  .back-photo{position:absolute;inset:0;background:linear-gradient(120deg,var(--photo-dark) 0%,#8a7463 30%,var(--photo-green) 65%,#9fb58a 100%)}
  .card--back .brand{left:34px;top:40px;font-size:20px}
  .back-band{position:absolute;right:0;top:0;width:390px;height:150px;background:linear-gradient(160deg,var(--blue-light),var(--blue))}
  .product-label{position:absolute;left:40px;top:26px;background:var(--grey);color:var(--white);font-size:32px;padding:8px 18px;letter-spacing:.5px}
  .product-tagline{position:absolute;left:40px;top:102px;color:var(--white);font-size:25px}
  .back-panel{position:absolute;right:0;top:150px;width:390px;height:140px;background:var(--brown);color:var(--white);padding:22px 40px}
  .back-phone{font-size:42px;font-weight:700;letter-spacing:1px}
  .back-cta{font-size:28px;margin-top:6px}
</style>
</head>
<body>
  <section class="card card--front" aria-label="Card front">
    <div class="front-band">
      <div class="brand"><span class="brand-mark"></span>B&amp;K INTERIORS</div>
    </div>
    <div class="offer-ribbon">
      <svg width="300" height="60" viewBox="0 0 300 60" aria-hidden="true">
        <polygon points="0,13 300,13 288,60 12,60" fill="#6b6c6e"/>
        <polygon points="0,13 10,0 10,13" fill="#4a4b4d"/>
        <polygon points="300,13 290,0 290,13" fill="#4a4b4d"/>
      </svg>
      <span>25% OFF</span>
    </div>
    <p class="offer-copy">Quality Custom Made Roller Blinds<br>Blockout • Screen • Light Filtering</p>
    <div class="badges" aria-hidden="true">
      <span class="badge"></span><span class="badge"></span><span class="badge"></span>
    </div>
    <p class="call-line">Call <strong>0400 123 456</strong> Today!</p>
  </section>

  <section class="card card--back" aria-label="Card back">
    <div class="back-photo" role="img" aria-label="Photo of a room with roller blinds over large windows looking onto garden greenery"></div>
    <div class="brand"><span class="brand-mark"></span>B&amp;K INTERIORS</div>
    <div class="back-band">
      <div class="product-label">ROLLER BLINDS</div>
      <div class="product-tagline">Huge Selection of Fabrics</div>
    </div>
    <div class="back-panel">
      <div class="back-phone">0400 123 456</div>
      <div class="back-cta">CALL TODAY!</div>
    </div>
  </section>
</body>
</html>
```